Hearthside Lending Relief

Please help us give our website a remake or a FACELIFT. It is not very good but it says what we need it to say. But the design is terrible.
I would like our new design font and logo to be used as the theme.

I also want more photos on the site.

I also want consistency with the pages so they look clean.

We want the professionals to do this, let's see what you got!

Thank you!
Updates

Project Deadline Extended
Reason: I can understand you want to be paid. So I will commit to the fee but I want you to have time to make a KICK ASS website for me dudes! Thanks

HI!  Just wanted to say thanks for your time on these.  A lot are great.  However the firefighters have nothing to do with Foreclosure.  We are saving peoples homes from the bank taking them and selling them.   I LOVE the house photos and the families on the website.  That is the direction we like.  THanks.

THANK U ALL FOR THE WORK!   I like a few ending in the numbers: 147  733  693  536  620  478  727  508     I will go over them and choose one soon.  Thank you.   You will be paid shortly. 

Requirements
Must have
• Bright, Upbeat photos. Color scheme should be in order. We like icons on the bottom. not just text.

```html
<!DOCTYPE html>
<html lang="en">
<head>
<meta charset="utf-8">
<title>Hearthside Lending Relief</title>
<link href="https://fonts.googleapis.com/css2?family=Figtree:wght@400;500;600;700;800;900&display=swap" rel="stylesheet">
<style>
  :root {
    --red: #e0141b;
    --red-dark: #b80d12;
    --ink: #1d1d1d;
    --text: #4d4d4d;
    --header-bg: #f1efec;
    --page-bg: #e4e4e4;
    --card: #ffffff;
    --panel: #efefef;
    --sky: #8fcbec;
    --navy: #17324d;
    --quote-text: #ffffff;
    --footer: #2e2e2e;
    --footer-text: #f2f2f2;
    --footer-muted: #8b8b8b;
    --font: "Figtree", Arial, sans-serif;
  }
  * { box-sizing: border-box; margin: 0; padding: 0; }
  html, body { width: 1134px; height: 1200px; overflow: hidden; }
  body {
    position: relative;
    font-family: var(--font);
    color: var(--text);
    background: var(--page-bg);
  }
  .site-header {
    position: absolute; left: 0; top: 0; width: 1134px; height: 147px;
    background: var(--header-bg);
  }
  .brand {
    position: absolute; left: 134px; top: 26px;
    display: flex; align-items: center; gap: 12px;
  }
  .brand-dot {
    width: 74px; height: 74px; border-radius: 50%;
    background: var(--red);
  }
  .brand-name {
    font-weight: 900; font-size: 24px; line-height: 24px;
    color: var(--ink); text-transform: uppercase; letter-spacing: 0.2px;
  }
  .language-note {
    position: absolute; left: 627px; top: 28px;
    font-weight: 800; font-size: 15px; color: var(--ink); letter-spacing: 0.6px;
  }
  .phone-icon { position: absolute; left: 803px; top: 23px; width: 32px; height: 32px; }
  .call-label {
    position: absolute; left: 843px; top: 18px;
    font-size: 13.5px; font-weight: 600; color: var(--ink); letter-spacing: 0.4px;
  }
  .call-number {
    position: absolute; left: 843px; top: 32px;
    font-size: 24px; font-weight: 500; color: var(--red);
  }
  .main-nav {
    position: absolute; left: 439px; top: 75px; width: 564px; height: 31px;
    display: flex; border-radius: 3px;
    background: linear-gradient(var(--red), var(--red-dark));
  }
  .main-nav a {
    display: flex; align-items: center; justify-content: center;
    color: #fff; text-decoration: none; font-size: 13.5px; font-weight: 500; letter-spacing: 0.4px;
    border-right: 1px solid rgba(0,0,0,0.25);
  }
  .main-nav a:last-child { border-right: none; }

  .content-card {
    position: absolute; left: 133px; top: 115px; width: 871px; height: 871px;
    background: var(--card); border-radius: 5px;
    box-shadow: 0 1px 4px rgba(0,0,0,0.18);
  }
  .hero {
    position: absolute; left: 9px; top: 9px; width: 853px; height: 315px; border-radius: 4px;
    background: linear-gradient(90deg, #8d8a6a 0%, #5f7040 35%, #7c8a4d 55%, #e3ddd2 62%, #d83438 70%, #c9272b 90%, #9aa06f 100%);
  }
  .welcome {
    position: absolute; left: 18px; top: 339px; width: 605px;
  }
  .welcome h1 {
    font-size: 18.5px; font-weight: 700; color: #555; letter-spacing: 0.4px;
  }
  .welcome h1 .accent { color: var(--red); }
  .welcome p {
    margin-top: 18px; font-size: 14px; line-height: 20.4px; color: var(--text);
  }
  .welcome p + p { margin-top: 20.4px; }
  .read-more {
    display: block; margin-top: 7px; font-size: 12px; color: var(--red); text-decoration: none;
  }
  .options {
    position: absolute; left: 17px; top: 615px; width: 601px; height: 240px;
    background: var(--panel); border-radius: 4px; padding: 14px 20px 0 19px;
  }
  .options-intro {
    font-size: 13.5px; font-weight: 700; line-height: 17px; color: #505050; width: 520px;
  }
  .options ul { list-style: none; margin-top: 9px; }
  .options li {
    position: relative; padding-left: 22px; font-size: 13.5px; line-height: 16px; color: #555;
    margin-bottom: 9px; width: 480px;
  }
  .options li::before {
    content: ""; position: absolute; left: 3px; top: 4px;
    border-left: 6px solid #b6b6b6; border-top: 4px solid transparent; border-bottom: 4px solid transparent;
  }
  .testimonials {
    position: absolute; left: 642px; top: 341px; width: 220px; height: 492px;
    background: var(--sky); border-radius: 4px; padding: 10px 13px 0 13px;
  }
  .testimonials h2 { font-size: 18.5px; font-weight: 700; color: var(--navy); }
  .quote { position: relative; padding-left: 28px; margin-top: 11px; }
  .quote + .quote { margin-top: 22px; }
  .quote::before {
    content: "\201C"; position: absolute; left: 0; top: -6px;
    font-size: 42px; font-weight: 700; color: #e9f5fb; line-height: 42px;
  }
  .quote p { font-size: 12.3px; line-height: 16px; color: var(--quote-text); }
  .quote cite { display: block; margin-top: 4px; font-style: normal; font-size: 11.5px; color: var(--navy); }

  .site-footer {
    position: absolute; left: 0; top: 1013px; width: 1134px; height: 187px;
    background: var(--footer); border-top: 4px solid var(--red);
    color: var(--footer-text);
  }
  .mail-art {
    position: absolute; left: 221px; top: 25px; width: 79px; height: 68px; border-radius: 6px;
    background: linear-gradient(135deg, #f2b43a 0%, #3aa9d8 45%, #2a86c2 100%);
  }
  .footer-email { position: absolute; left: 133px; top: 97px; font-size: 13px; letter-spacing: 0.3px; }
  .footer-label { position: absolute; top: 33px; font-size: 13px; font-weight: 500; letter-spacing: 0.5px; }
  .mailing-label { left: 423px; }
  .email-field {
    position: absolute; left: 423px; top: 48px; width: 173px; height: 23px; border-radius: 4px;
    background: #8a8a8a; color: #e6e6e6; font-size: 11.5px; padding: 5px 9px;
  }
  .join-button {
    position: absolute; left: 423px; top: 81px; width: 52px; height: 23px; border-radius: 3px;
    background: linear-gradient(#f4f4f4, #c9c9c9); color: #333; font-size: 14px; text-align: center; line-height: 23px;
  }
  .follow-label { left: 642px; }
  .social-links { position: absolute; left: 642px; top: 49px; display: flex; gap: 9px; }
  .social-links span { width: 28px; height: 28px; border-radius: 3px; background: #6f7f8f; }
  .office { position: absolute; left: 784px; top: 33px; font-size: 13.5px; line-height: 20.4px; letter-spacing: 0.3px; }
  .footer-rule { position: absolute; left: 133px; top: 136px; width: 870px; height: 1px; background: #464646; }
  .copyright {
    position: absolute; left: 0; top: 155px; width: 1134px; text-align: center;
    font-size: 11.5px; color: var(--footer-muted); letter-spacing: 0.3px;
  }
</style>
</head>
<body>
  <header class="site-header">
    <div class="brand">
      <span class="brand-dot"></span>
      <span class="brand-name">Hearthside<br>Lending<br>Relief</span>
    </div>
    <div class="language-note">HABLAMOS ESPANOL</div>
    <svg class="phone-icon" viewBox="0 0 32 32" aria-hidden="true">
      <rect width="32" height="32" rx="5" fill="#e0141b"/>
      <path d="M10 8c1-1 2-1 3 0l2 3c.6 1 .3 1.8-.4 2.4l-1 .8c.8 2 2.3 3.6 4.2 4.4l.8-1c.6-.7 1.4-1 2.4-.4l3 2c1 .7 1 1.8 0 2.8l-1.5 1.5c-1.5 1.3-4 .8-7-1.6-3-2.4-5.6-5.6-6.4-8.6-.4-1.6-.2-2.8.6-3.6z" fill="#fff"/>
    </svg>
    <div class="call-label">CALL TOLL FREE NOW</div>
    <div class="call-number">877-555-0148</div>
    <nav class="main-nav">
      <a href="#" style="width:82px">HOME</a>
      <a href="#" style="width:100px">ABOUT US</a>
      <a href="#" style="width:99px">SERVICES</a>
      <a href="#" style="width:118px">CONTACT US</a>
      <a href="#" style="width:165px">OWNER OPTIONS</a>
    </nav>
  </header>

  <main class="content-card">
    <div class="hero" role="img" aria-label="Photo of a house front lawn with a red foreclosure for-sale sign"></div>

    <section class="welcome">
      <h1>WELCOME TO <span class="accent">HEARTHSIDE</span> LENDING <span class="accent">RELIEF</span></h1>
      <p>HEARTHSIDE LENDING RELIEF specializes in assisting homeowners who are in FORECLOSURE, by offering solid alternatives to losing your home in a Trustee Sale.&nbsp; Having your home foreclosed on can damage your credit for up to 7 years.&nbsp; Most foreclosures end with the home owner being evicted from their home, leaving them with no money, no place to live and without ample time to safely remove their possessions from their home.&nbsp; There is no need to have this happen to you.&nbsp; No matter what part of foreclosure process you are in, WE CAN HELP!</p>
      <p>If you have received a Notice of Default (NOD) or Notice of Trustee Sale (NTS), you have options.&nbsp; Contact us today to speak to one of our licensed specialist, and let us help you put this situation behind you.</p>
      <a class="read-more" href="#">Read more</a>
    </section>

    <section class="options">
      <p class="options-intro">You may not know it but there are several great options available to you.&nbsp; We can help you determine which one will work best for you FREE OF CHARGE:</p>
      <ul>
        <li>Bringing your mortgage current to stop the foreclosure</li>
        <li>HLR can purchase your home with CASH in 7-10 days</li>
        <li>Financing/Purchase Options</li>
        <li>Relocations Assistance - if needed</li>
        <li>Remodel your home to increase it's value</li>
        <li>Many other options are available - We realize that all of our clients have different needs.&nbsp; We look at your individual needs to customize a solution just for you.</li>
      </ul>
    </section>

    <aside class="testimonials">
      <h2>Testimonials</h2>
      <blockquote class="quote">
        <p>I'd like to express my gratitude to you and your company and I have to add, for all of the trustworthy and reliable service that you bring to the public.&nbsp; Your company helped put me back together, you in particular are wesome! Thank you again Theo.</p>
        <cite>Rosalind</cite>
      </blockquote>
      <blockquote class="quote">
        <p>Hearthside Lending Relief has been an absolute life saver for me and my family.&nbsp; Their services have changed everything.&nbsp; Instead of my house going into foreclosure and losing everything I own, I now have a chance to start over and the money to do it with!&nbsp; They've been fast, friendly and efficient.&nbsp; I would recommend their services to anyone facing foreclosure.</p>
        <cite>Dana K.</cite>
      </blockquote>
    </aside>
  </main>

  <footer class="site-footer">
    <div class="mail-art" role="img" aria-label="Illustration of a blue envelope with a yellow hand"></div>
    <div class="footer-email">INFO@HEARTHSIDELENDINGRELIEF.COM</div>

    <div class="footer-label mailing-label">JOIN OUR MAILING LIST</div>
    <div class="email-field">Your e-mail address</div>
    <div class="join-button">Join</div>

    <div class="footer-label follow-label">FOLLOW US</div>
    <div class="social-links">
      <span role="img" aria-label="Social link 1"></span>
      <span role="img" aria-label="Social link 2"></span>
      <span role="img" aria-label="Social link 3"></span>
    </div>

    <address class="office" style="font-style:normal">
      HEARTHSIDE LENDING RELIEF<br>
      118 Harbor View Avenue Suite 300<br>
      Linden Bay, CA 90417<br>
      877-555-0148
    </address>

    <div class="footer-rule"></div>
    <div class="copyright">© 2012. HEARTHSIDELENDINGRELIEF.COM. All rights reserved.&nbsp; Reserved | Privacy Policy</div>
  </footer>
</body>
</html>
```